Global Beard Oil Review Business needs a refresh

topwhiskertonic.net is a global business who's mission is to curate all available beard oils from around the world, review and grade them and present this curated collection to the user of the website.

The scope of this job includes the web site design and the design of a suitable logo to be used in the site header.

The existing site can be seen on http://topwhiskertonic.net, however this is a mock-up only the style and logo should NOT be used. This is to give you an idea of the concept of the site only.

This job is for PSD design only.

See attached design brief for detailed design requirements.
Updates

Project Deadline Extended
Reason: Extending deadline by 5 days to allow for final submissions

Target Market(s)

Men's grooming / retail

Industry/Entity Type

Retail

Number of Pages Required

2 page

Font styles to use
Sans Serif

Requirements
Must have
• 1) Comparison Table
• 2) Side Bar
• 3) Header area
• 4) Photo of Delvin Marsk (attached - can be circular or "cut-out")
• 5) Cool beard-oriented custom design background (e.g., stylistic black/brown on brown/orange beard background. I envision this beard background "drawing" rather than photo based)
• (see attached design requirements for details)
Nice to have
• Signature style writing at top with name "Delvin Marsk"
Should not have
• Do NOT use the look & feel or logo from the existing site.

```html
<!DOCTYPE html>
<html lang="en">
<head>
<meta charset="utf-8">
<title>Top Whisker Tonic – Beard Oil Comparison</title>
<link rel="stylesheet" href="https://fonts.googleapis.com/css2?family=Source+Sans+3:wght@300;400;600;700&display=swap">
<style>
:root{
  --ink:#0d0d0d;
  --orange:#ff7f00;
  --orange-btn:#f47a10;
  --brown:#8a5a2b;
  --dark-band:#2b2b2b;
  --text:#555;
  --line:#e3e3e3;
  --white:#fff;
  --wood-dark:#2e2e2e;
  --wood-mid:#6f6f6f;
  --wood-light:#b4b4b4;
}
*{box-sizing:border-box;margin:0;padding:0}
html,body{width:1200px;height:2230px;overflow:hidden}
body{position:relative;font-family:"Source Sans 3",Arial,sans-serif;color:var(--text);background:var(--wood-dark)}
.page-backdrop{position:absolute;inset:0;
  background:
    radial-gradient(ellipse 260px 420px at 60px 1000px,rgba(20,20,20,.75),transparent 70%),
    radial-gradient(ellipse 220px 300px at 1140px 500px,rgba(15,15,15,.7),transparent 70%),
    radial-gradient(ellipse 260px 380px at 1150px 1400px,rgba(230,230,230,.45),transparent 70%),
    radial-gradient(ellipse 300px 500px at 70px 1600px,rgba(210,210,210,.4),transparent 70%),
    repeating-linear-gradient(100deg,rgba(255,255,255,.05) 0 3px,transparent 3px 14px,rgba(0,0,0,.08) 14px 17px,transparent 17px 40px),
    linear-gradient(160deg,var(--wood-dark) 0%,var(--wood-mid) 25%,var(--wood-light) 45%,var(--wood-mid) 65%,var(--wood-light) 80%,var(--wood-dark) 100%)}

.site-header{position:absolute;left:0;top:0;width:1200px;height:103px;background:var(--ink)}
.brand{position:absolute;left:134px;top:36px;font-size:23px;font-weight:700;color:var(--white);letter-spacing:.2px}
.main-nav{position:absolute;left:390px;top:45px;display:flex;gap:24px;font-size:10.5px;font-weight:600;color:var(--white)}
.main-nav .active{color:var(--orange)}
.review-badge{position:absolute;left:850px;top:30px;width:218px;height:42px;background:var(--orange);border-radius:4px;color:var(--white)}
.review-badge .portrait{position:absolute;left:-2px;top:-4px;width:50px;height:50px;border-radius:50%;background:radial-gradient(circle,#8a4f3a,#3a2a22)}
.review-badge .title{position:absolute;left:56px;top:8px;font-size:11px;font-weight:700}
.review-badge .by{position:absolute;left:56px;top:22px;font-size:10px;font-style:italic}

.hero{position:absolute;left:131px;top:119px;width:937px;height:446px;background:linear-gradient(120deg,#3b2516 0%,#7a4a26 40%,#5a3620 70%,#2a1f1c 100%)}
.hero h1{position:absolute;left:0;width:100%;top:190px;text-align:center;font-weight:300;font-size:62px;color:var(--white);letter-spacing:1px}
.hero .arrow{position:absolute;top:218px}
.hero-caption{position:absolute;left:131px;top:565px;width:937px;height:149px;background:linear-gradient(90deg,#3a2210,#4a2c14 50%,#3a2210);color:var(--white);text-align:center}
.hero-caption h2{margin-top:28px;font-size:19px;font-weight:600}
.hero-caption p{margin:12px auto 0;width:840px;font-size:12.5px;line-height:24px;color:#e8ddd2}

.comparison{position:absolute;left:132px;top:732px;width:702px;height:1365px;background:var(--white)}
.comparison-title{height:56px;background:var(--orange);color:var(--white);font-size:25px;font-weight:400;padding:11px 12px;letter-spacing:.3px}
.controls{position:absolute;top:73px;right:12px;display:flex;align-items:center;gap:12px;font-size:9.5px;font-weight:600;color:#555}
.select{width:166px;height:26px;border:1px solid var(--line);font-weight:400;color:#aaa;font-size:9.5px;padding:6px;position:relative}
.select.small{width:110px}
.select::after{content:"";position:absolute;right:8px;top:9px;width:4px;height:4px;border-right:1px solid #666;border-bottom:1px solid #666;transform:rotate(45deg)}
.controls .label{margin-left:14px}

.oil-table{position:absolute;left:12px;top:113px;width:678px;border-collapse:collapse;table-layout:fixed;font-size:9.5px;color:#777}
.oil-table .group th{height:38px;text-align:left;padding-left:16px;font-size:12px;font-weight:400;color:var(--white)}
.oil-table .group .info{background:var(--dark-band)}
.oil-table .group .review{background:var(--brown)}
.oil-table .cols th{height:42px;font-size:8.5px;font-weight:600;color:#666;border:1px solid var(--line);text-align:center;line-height:11px}
.oil-table td{height:69px;border:1px solid var(--line);text-align:center;line-height:11px}
.bottle{display:inline-block;width:16px;height:34px;border-radius:3px 3px 2px 2px;background:linear-gradient(#3a2a20 0 30%,#c98a3c 30%)}
.buy{display:inline-block;width:66px;height:26px;line-height:26px;background:var(--orange-btn);color:var(--white);border-radius:3px;font-size:10.5px}

.pager{position:absolute;top:1312px;right:14px;display:flex;gap:9px;font-size:8px;color:#555}
.pager span{width:21px;height:20px;border:1px solid #ccc;border-radius:2px;text-align:center;line-height:18px}
.pager .current{background:#333;color:var(--white);border-color:#333}
.pager .gap{border:none;width:14px}

.sidebar{position:absolute;left:846px;top:732px;width:222px;height:1365px;background:var(--white)}
.search{position:absolute;left:11px;top:19px;width:200px;height:37px;border:1px solid var(--line);font-size:12px;color:#777;padding:10px 10px}
.search svg{position:absolute;right:10px;top:11px}
.widget h3{font-size:18px;font-weight:400;color:var(--brown);padding:0 10px;height:44px;border-bottom:1px solid var(--line);line-height:44px}
.widget ul{list-style:none;padding:14px 12px}
.widget li{position:relative;padding-left:20px;font-size:13px;color:#666;line-height:21px;margin-bottom:12px}
.recent li{margin-bottom:18px}
.widget li::before{content:"";position:absolute;left:0;top:6px;border-left:6px solid #777;border-top:4px solid transparent;border-bottom:4px solid transparent}
.categories{position:absolute;top:68px;width:100%}
.recent{position:absolute;top:196px;width:100%}
.archives{position:absolute;top:562px;width:100%}

.site-footer{position:absolute;left:0;top:2132px;width:1200px;height:98px;background:var(--ink);color:var(--white);text-align:center;font-size:10px;font-weight:600}
.footer-nav{margin-top:31px;word-spacing:2px}
.footer-nav span{margin:0 10px}
.copyright{margin-top:12px;font-size:9.5px}
</style>
</head>
<body>
<div class="page-backdrop" role="img" aria-label="Black and white weathered wooden surface with grooming tools"></div>

<header class="site-header">
  <div class="brand">TOPWHISKERTONIC</div>
  <nav class="main-nav">
    <span class="active">FRONT PAGE</span><span>ABOUT ME</span><span>BEARD OIL REVIEW METHODOLOGY</span><span>CHARTER</span><span>BLOG</span>
  </nav>
  <div class="review-badge">
    <div class="portrait" role="img" aria-label="Portrait of Delvin Marsk"></div>
    <div class="title">GLOBAL BEARD OIL REVIEW</div>
    <div class="by">with Delvin Marsk</div>
  </div>
</header>

<section class="hero" role="img" aria-label="Wooden shaving bowl and leather braces on a wood table">
  <svg class="arrow" style="left:30px" width="14" height="24" viewBox="0 0 14 24"><path d="M12 2 2 12l10 10" fill="none" stroke="#fff" stroke-width="2.5"/></svg>
  <h1>TOP WHISKER TONIC</h1>
  <svg class="arrow" style="right:30px" width="14" height="24" viewBox="0 0 14 24"><path d="m2 2 10 10L2 22" fill="none" stroke="#fff" stroke-width="2.5"/></svg>
</section>
<section class="hero-caption">
  <h2>THE WORLD’S #1 BEARD OIL AUTHORITY</h2>
  <p>Here is the master list of beard oils reviewed to date. You can link directly to the corresponding review by clicking on the name of the beard oil. In accordance with our charter, we are actively working to locate and review every single beard oil available on the planet Earth.</p>
</section>

<main class="comparison">
  <div class="comparison-title">BEARD OIL COMPARISON TABLE</div>
  <div class="controls">
    <span class="label">FILTERS</span><div class="select">Any Categories</div>
    <span class="label">SORT BY</span><div class="select small">Any price</div>
  </div>
  <table class="oil-table">
    <colgroup>
      <col style="width:81px"><col style="width:60px"><col style="width:54px"><col style="width:43px"><col style="width:58px"><col style="width:60px"><col style="width:45px"><col style="width:85px"><col style="width:37px"><col style="width:67px"><col style="width:88px">
    </colgroup>
    <thead>
      <tr class="group"><th class="info" colspan="6">INFORMATION</th><th class="review" colspan="5">REVIEW</th></tr>
      <tr class="cols"><th>SUPPLIER</th><th>NAME</th><th>PHOTO</th><th>ORIGIN</th><th>BASE OIL</th><th>SCENT</th><th>AROMA</th><th>THERAPEUTIC<br>AFFECT</th><th>VALUE</th><th>OVERALL</th><th>LINKS</th></tr>
    </thead>
    <tbody>
      <tr><td>Northcrest Men's Grooming</td><td>Northcrest Beard Oil</td><td><span class="bottle" role="img" aria-label="Beard oil bottle"></span></td><td>USA</td><td>Northcrest Beard Oil</td><td>Northcrest Beard Oil</td><td>7</td><td>2</td><td>2</td><td>11</td><td><span class="buy">BUY NOW</span></td></tr>
      <tr><td>Northcrest Men's Grooming</td><td>Northcrest Beard Oil</td><td><span class="bottle" role="img" aria-label="Beard oil bottle"></span></td><td>USA</td><td>Northcrest Beard Oil</td><td>Northcrest Beard Oil</td><td>7</td><td>2</td><td>2</td><td>11</td><td><span class="buy">BUY NOW</span></td></tr>
      <tr><td>Northcrest Men's Grooming</td><td>Northcrest Beard Oil</td><td><span class="bottle" role="img" aria-label="Beard oil bottle"></span></td><td>USA</td><td>Northcrest Beard Oil</td><td>Northcrest Beard Oil</td><td>7</td><td>2</td><td>2</td><td>11</td><td><span class="buy">BUY NOW</span></td></tr>
      <tr><td>Northcrest Men's Grooming</td><td>Northcrest Beard Oil</td><td><span class="bottle" role="img" aria-label="Beard oil bottle"></span></td><td>USA</td><td>Northcrest Beard Oil</td><td>Northcrest Beard Oil</td><td>7</td><td>2</td><td>2</td><td>11</td><td><span class="buy">BUY NOW</span></td></tr>
      <tr><td>Northcrest Men's Grooming</td><td>Northcrest Beard Oil</td><td><span class="bottle" role="img" aria-label="Beard oil bottle"></span></td><td>USA</td><td>Northcrest Beard Oil</td><td>Northcrest Beard Oil</td><td>7</td><td>2</td><td>2</td><td>11</td><td><span class="buy">BUY NOW</span></td></tr>
      <tr><td>Northcrest Men's Grooming</td><td>Northcrest Beard Oil</td><td><span class="bottle" role="img" aria-label="Beard oil bottle"></span></td><td>USA</td><td>Northcrest Beard Oil</td><td>Northcrest Beard Oil</td><td>7</td><td>2</td><td>2</td><td>11</td><td><span class="buy">BUY NOW</span></td></tr>
      <tr><td>Northcrest Men's Grooming</td><td>Northcrest Beard Oil</td><td><span class="bottle" role="img" aria-label="Beard oil bottle"></span></td><td>USA</td><td>Northcrest Beard Oil</td><td>Northcrest Beard Oil</td><td>7</td><td>2</td><td>2</td><td>11</td><td><span class="buy">BUY NOW</span></td></tr>
      <tr><td>Northcrest Men's Grooming</td><td>Northcrest Beard Oil</td><td><span class="bottle" role="img" aria-label="Beard oil bottle"></span></td><td>USA</td><td>Northcrest Beard Oil</td><td>Northcrest Beard Oil</td><td>7</td><td>2</td><td>2</td><td>11</td><td><span class="buy">BUY NOW</span></td></tr>
      <tr><td>Northcrest Men's Grooming</td><td>Northcrest Beard Oil</td><td><span class="bottle" role="img" aria-label="Beard oil bottle"></span></td><td>USA</td><td>Northcrest Beard Oil</td><td>Northcrest Beard Oil</td><td>7</td><td>2</td><td>2</td><td>11</td><td><span class="buy">BUY NOW</span></td></tr>
      <tr><td>Northcrest Men's Grooming</td><td>Northcrest Beard Oil</td><td><span class="bottle" role="img" aria-label="Beard oil bottle"></span></td><td>USA</td><td>Northcrest Beard Oil</td><td>Northcrest Beard Oil</td><td>7</td><td>2</td><td>2</td><td>11</td><td><span class="buy">BUY NOW</span></td></tr>
      <tr><td>Northcrest Men's Grooming</td><td>Northcrest Beard Oil</td><td><span class="bottle" role="img" aria-label="Beard oil bottle"></span></td><td>USA</td><td>Northcrest Beard Oil</td><td>Northcrest Beard Oil</td><td>7</td><td>2</td><td>2</td><td>11</td><td><span class="buy">BUY NOW</span></td></tr>
      <tr><td>Northcrest Men's Grooming</td><td>Northcrest Beard Oil</td><td><span class="bottle" role="img" aria-label="Beard oil bottle"></span></td><td>USA</td><td>Northcrest Beard Oil</td><td>Northcrest Beard Oil</td><td>7</td><td>2</td><td>2</td><td>11</td><td><span class="buy">BUY NOW</span></td></tr>
      <tr><td>Northcrest Men's Grooming</td><td>Northcrest Beard Oil</td><td><span class="bottle" role="img" aria-label="Beard oil bottle"></span></td><td>USA</td><td>Northcrest Beard Oil</td><td>Northcrest Beard Oil</td><td>7</td><td>2</td><td>2</td><td>11</td><td><span class="buy">BUY NOW</span></td></tr>
      <tr><td>Northcrest Men's Grooming</td><td>Northcrest Beard Oil</td><td><span class="bottle" role="img" aria-label="Beard oil bottle"></span></td><td>USA</td><td>Northcrest Beard Oil</td><td>Northcrest Beard Oil</td><td>7</td><td>2</td><td>2</td><td>11</td><td><span class="buy">BUY NOW</span></td></tr>
      <tr><td>Northcrest Men's Grooming</td><td>Northcrest Beard Oil</td><td><span class="bottle" role="img" aria-label="Beard oil bottle"></span></td><td>USA</td><td>Northcrest Beard Oil</td><td>Northcrest Beard Oil</td><td>7</td><td>2</td><td>2</td><td>11</td><td><span class="buy">BUY NOW</span></td></tr>
      <tr><td>Northcrest Men's Grooming</td><td>Northcrest Beard Oil</td><td><span class="bottle" role="img" aria-label="Beard oil bottle"></span></td><td>USA</td><td>Northcrest Beard Oil</td><td>Northcrest Beard Oil</td><td>7</td><td>2</td><td>2</td><td>11</td><td><span class="buy">BUY NOW</span></td></tr>
    </tbody>
  </table>
  <div class="pager">
    <span>‹</span><span>1</span><span>2</span><span>3</span><span class="current">4</span><span>5</span><span class="gap">....</span><span>15</span><span>30</span><span>45</span><span>›</span>
  </div>
</main>

<aside class="sidebar">
  <div class="search">SEARCH
    <svg width="13" height="13" viewBox="0 0 13 13"><circle cx="5.5" cy="5.5" r="4" fill="none" stroke="#ff7f00" stroke-width="2"/><path d="m8.5 8.5 3.5 3.5" stroke="#ff7f00" stroke-width="2"/></svg>
  </div>
  <section class="widget categories">
    <h3>CATEGORIES</h3>
    <ul><li>Articles</li><li>Reviews</li></ul>
  </section>
  <section class="widget recent">
    <h3>RECENT POSTS</h3>
    <ul>
      <li>Outback Face/Beard Oil by Everbody Soaps</li>
      <li>Northcrest Beard Oil by Northcrest Men's Grooming</li>
      <li>Timberline Oil by Allied Beard Co.</li>
      <li>Forester by The Bristled Rogue</li>
      <li>Our Charter</li>
    </ul>
  </section>
  <section class="widget archives">
    <h3>ARCHIVES</h3>
    <ul><li>February 2016</li><li>January 2016</li></ul>
  </section>
</aside>

<footer class="site-footer">
  <div class="footer-nav">FRONT PAGE<span>|</span>ABOUT ME<span>|</span>BEARD OIL REVIEW METHODOLOGY<span>|</span>CHARTER<span>|</span>BLOG</div>
  <div class="copyright">© 2016 COMPANY NAME | ALL RIGHTS RESERVED</div>
</footer>
</body>
</html>
```